Need Flyer for Our Real estate Agency

Need to run General Campaign for our agency with Start of New Year as our theme ..Must have an agent's picture on the DL..
Address:
27 / 486Brindle rd, Marsden VIC 3047
Ph:03 9412 7306
email:info@kovalinrealestate.com.au
www.kovalinrealestate.com.au
Something like as attached picture..
Target Market(s)
Home Buyers
Industry/Entity Type
Real Estate Agent
Requirements
Must have
- Our Logo Colours

```html
<!DOCTYPE html>
<html lang="en">
<head>
<meta charset="utf-8">
<title>Kovalin Real Estate – New Year DL Flyer</title>
<link rel="stylesheet" href="https://fonts.googleapis.com/css2?family=Lato:wght@300;400&family=Open+Sans:wght@400;700&display=swap">
<style>
  :root{
    --navy:#0c2260;
    --navy-deep:#06164a;
    --navy-light:#17367f;
    --maroon:#7a1420;
    --swoosh:#d6d9df;
    --white:#ffffff;
    --stage:#d9dadc;
    --photo-sky:#7f9bc4;
    --photo-house:#c9c4b8;
    --photo-lawn:#4d6b3a;
    --photo-skin:#d9a68a;
    --photo-suit:#1c2d4f;
    --photo-toy:#d4524e;
  }
  *{margin:0;padding:0;box-sizing:border-box}
  html,body{width:1183px;height:1200px;overflow:hidden;background:var(--stage)}
  .flyer{position:absolute;left:81px;width:1051px;height:500px;overflow:hidden;
    box-shadow:0 6px 10px rgba(0,0,0,.25);color:var(--white);font-family:'Lato',sans-serif}
  .flyer--front{top:66px}
  .flyer--back{top:644px}
  .flyer__art{position:absolute;inset:0;width:100%;height:100%}
  .brand{position:absolute;text-align:center;font-family:'Lato',sans-serif;font-weight:400;color:var(--white)}
  .brand__name{display:block;font-size:56px;letter-spacing:6px;line-height:1}
  .brand__sub{display:block;font-size:11px;letter-spacing:3px;margin-top:10px}
  .flyer--front .brand{left:88px;width:400px;top:128px}
  .flyer--back .brand{left:564px;width:400px;top:128px}
  .headline{position:absolute;left:48px;width:480px;top:234px;text-align:center;
    font-weight:300;font-size:34px;line-height:48px}
  .tagline{position:absolute;left:8px;width:560px;top:354px;text-align:center;
    font-family:'Open Sans',sans-serif;font-size:16.5px}
  .tagline strong{font-weight:700}
  .call-pill{position:absolute;left:92px;top:407px;width:396px;height:48px;border-radius:24px;
    background:var(--white);color:var(--maroon);font-family:'Open Sans',sans-serif;font-weight:700;
    font-size:22px;display:flex;align-items:center;justify-content:center;gap:8px;
    box-shadow:0 3px 6px rgba(0,0,0,.3)}
  .call-pill svg{width:22px;height:22px}
  .appraisal{position:absolute;left:92px;width:396px;top:464px;text-align:center;font-size:19px}
  .agent-title{position:absolute;left:603px;top:240px;font-size:22px;font-weight:400}
  .contact-list{position:absolute;left:603px;top:288px;list-style:none;font-size:19px}
  .contact-list li{display:flex;align-items:center;gap:12px;height:39px}
  .contact-list svg{width:20px;height:20px;flex:none}
  .address{position:absolute;left:420px;width:631px;top:453px;text-align:center;font-size:19px}
</style>
</head>
<body>

<section class="flyer flyer--front">
  <svg class="flyer__art" viewBox="0 0 1051 500" preserveAspectRatio="none">
    <defs>
      <linearGradient id="navyFront" x1="0" y1="0" x2="1" y2="1">
        <stop offset="0" stop-color="var(--navy-deep)"/>
        <stop offset=".6" stop-color="var(--navy)"/>
        <stop offset="1" stop-color="var(--navy-light)"/>
      </linearGradient>
      <linearGradient id="agentPhoto" x1="0" y1="0" x2="0" y2="1">
        <stop offset="0" stop-color="var(--photo-sky)"/>
        <stop offset=".45" stop-color="var(--photo-house)"/>
        <stop offset=".75" stop-color="var(--photo-suit)"/>
        <stop offset="1" stop-color="var(--photo-lawn)"/>
      </linearGradient>
    </defs>
    <rect width="1051" height="500" fill="url(#navyFront)"/>
    <rect y="426" width="700" height="74" fill="var(--maroon)"/>
    <rect y="424" width="700" height="2" fill="var(--white)"/>
    <path d="M600 0 C520 150 545 380 625 500 L665 500 C585 380 562 150 642 0 Z" fill="var(--swoosh)"/>
    <path d="M604 0 C524 150 549 380 629 500" fill="none" stroke="var(--white)" stroke-width="2"/>
    <path d="M642 0 C562 150 585 380 665 500 L1051 500 L1051 0 Z" fill="url(#agentPhoto)"
      role="img" aria-label="Photo of the agent in a blue suit smiling in front of a lit two-storey family home at dusk"/>
  </svg>

  <div class="brand">
    <span class="brand__name">KOVALIN</span>
    <span class="brand__sub">REAL ESTATE</span>
  </div>

  <h1 class="headline">Curios to know what your<br>home is worth?</h1>
  <p class="tagline">START OF NEW YEAR WITH <strong>ARJUN MALHOTRA</strong> AND FIND OUT!</p>

  <div class="call-pill">
    <span>CALL ME NOW!</span>
    <svg viewBox="0 0 24 24" aria-hidden="true"><circle cx="12" cy="12" r="10" fill="none" stroke="currentColor" stroke-width="2"/><path d="M8.5 7.5l1.8-.4 1 2.4-1.1.9a6 6 0 0 0 3.4 3.4l.9-1.1 2.4 1-.4 1.8c-4.6.3-8.3-3.4-8-8z" fill="currentColor"/></svg>
    <span>0412 583 906</span>
  </div>
  <p class="appraisal">For Free property Appraisal</p>
</section>

<section class="flyer flyer--back">
  <svg class="flyer__art" viewBox="0 0 1051 500" preserveAspectRatio="none">
    <defs>
      <linearGradient id="navyBack" x1="0" y1="0" x2="1" y2="1">
        <stop offset="0" stop-color="var(--navy-deep)"/>
        <stop offset=".6" stop-color="var(--navy)"/>
        <stop offset="1" stop-color="var(--navy-light)"/>
      </linearGradient>
      <radialGradient id="handsPhoto" cx=".45" cy=".55" r=".7">
        <stop offset="0" stop-color="var(--photo-toy)"/>
        <stop offset=".35" stop-color="var(--photo-skin)"/>
        <stop offset="1" stop-color="var(--photo-suit)"/>
      </radialGradient>
    </defs>
    <rect width="1051" height="500" fill="url(#navyBack)"/>
    <rect y="430" width="1051" height="70" fill="var(--maroon)"/>
    <rect y="428" width="1051" height="2" fill="var(--white)"/>
    <path d="M300 0 L420 0 C520 120 510 380 445 500 L420 500 C470 350 440 100 300 0 Z" fill="var(--swoosh)"/>
    <path d="M420 0 C520 120 510 380 445 500" fill="none" stroke="var(--white)" stroke-width="2"/>
    <path d="M0 0 L300 0 C440 100 470 350 420 500 L0 500 Z" fill="url(#handsPhoto)"
      role="img" aria-label="Photo of two hands sheltering a small red toy house"/>
  </svg>

  <div class="brand">
    <span class="brand__name">KOVALIN</span>
    <span class="brand__sub">REAL ESTATE</span>
  </div>

  <p class="agent-title">Arjun Malhotra, Director</p>
  <ul class="contact-list">
    <li>
      <svg viewBox="0 0 24 24" aria-hidden="true"><circle cx="12" cy="12" r="10" fill="none" stroke="#fff" stroke-width="2"/><path d="M8.5 7.5l1.8-.4 1 2.4-1.1.9a6 6 0 0 0 3.4 3.4l.9-1.1 2.4 1-.4 1.8c-4.6.3-8.3-3.4-8-8z" fill="#fff"/></svg>
      <span>03 9412 7306</span>
    </li>
    <li>
      <svg viewBox="0 0 24 24" aria-hidden="true"><circle cx="12" cy="12" r="10" fill="#fff"/><rect x="7" y="8.5" width="10" height="7" rx="1" fill="var(--navy)"/><path d="M7.5 9l4.5 3.5L16.5 9" fill="none" stroke="#fff" stroke-width="1.2"/></svg>
      <span>arjun.malhotra@kovalinrealestate.com.au</span>
    </li>
    <li>
      <svg viewBox="0 0 24 24" aria-hidden="true"><circle cx="12" cy="12" r="10" fill="#fff"/><g fill="none" stroke="var(--navy)" stroke-width="1.2"><circle cx="12" cy="12" r="6"/><ellipse cx="12" cy="12" rx="2.6" ry="6"/><path d="M6 12h12"/></g></svg>
      <span>www.kovalinrealestate.com.au</span>
    </li>
  </ul>

  <p class="address">27/486 Brindle Rd Marsden, Victoria, Australia 3047</p>
</section>

</body>
</html>
```